I need a logo design for a new company based in Tucson called "Mindtrail Lee Corwin". I am a psychotherapist that specializes in clinical psychology with athletes and performers. The final design should incorporate the psychology symbol as a watermark. The logo should convey movement and fluidity. "Mindtrail" is a bit of a play on words combining psychology (head) with sports (coach). Other design interests include mid-century, Harold Ames Whitby. I will want to use the logo for business cards, letterhead and marketing brochures. I will put together a website at a later date. I am attaching a file with some pertinent information for the business card. Thank you.
Lee Corwin
mindtrailleecorwin@quillpost.net

Thank you all for the submissions so far.  I have submitted an additional file with a draft of a new design idea.  Since "mindtrail" is a bit of a play on words, I would like to see something with the two "H's" look something like quotation marks.  If the psychology logo is to be included at all, it needs to be less prominent.     Thank you all.  Lee                               

Target Market(s)

1) Adolescent and adult athletes and performers who are looking to increase their level of performance (Sport and Performance Psychology)
2) Adult psychotherapy patients (Clinical psychology)

Industry/Entity Type

Marketing

Colors

Designer to choose colors to be used in the design.

Requirements
Must have
• 1) Since "mindtrail" is a bit of a play on words, The "H's" need to be in a font that looks somewhat like quotation marks.

Nice to have
• Logo on one side. All other info on the backside?

```html
<!DOCTYPE html>
<html lang="en">
<head>
<meta charset="utf-8">
<title>Mindtrail – Business Card</title>
<link rel="stylesheet" href="https://fonts.googleapis.com/css2?family=Libre+Baskerville:ital,wght@0,400;0,700;1,700&family=Lato:wght@400;700&display=swap">
<style>
  :root{
    --green:#3a9a45;
    --green-mid:#5cbf6a;
    --green-light:#9bd7a4;
    --paper:#ffffff;
    --grey-mark:#c4c4c4;
    --backdrop:#e9e9e6;
    --ink-light:#ffffff;
  }
  *{margin:0;padding:0;box-sizing:border-box}
  html,body{width:1200px;height:1000px;overflow:hidden}
  body{background:var(--backdrop);position:relative;font-family:"Lato",sans-serif}
  .card{position:absolute;left:250px;width:700px;height:400px;overflow:hidden;
        background:var(--paper);box-shadow:0 6px 18px rgba(0,0,0,.18)}
  .card--front{top:60px}
  .card--back{top:540px;background:var(--green)}
  .card__shape{position:absolute;inset:0;width:100%;height:100%}
  .brand{position:absolute;display:flex;flex-direction:column;align-items:center}
  .brand__dot{width:90px;height:90px;border-radius:50%;background:var(--grey-mark);margin-bottom:18px}
  .brand__name{font-family:"Libre Baskerville",serif;font-weight:700;color:var(--green);
               letter-spacing:1px;line-height:1}
  .card--front .brand{left:330px;top:95px}
  .card--front .brand__name{font-size:50px}
  .card--back .brand{left:40px;top:225px}
  .card--back .brand__dot{width:64px;height:64px;margin-bottom:12px}
  .card--back .brand__name{font-size:34px}
  .details{position:absolute;left:330px;top:44px;width:340px;color:var(--ink-light);text-align:center}
  .details__name{font-family:"Libre Baskerville",serif;font-style:italic;font-weight:700;font-size:24px}
  .details__name small{font-style:normal;font-size:18px;margin-left:8px}
  .details__role{font-size:14px;margin-top:6px;line-height:1.5}
  .contact{list-style:none;margin-top:30px;font-size:15px;line-height:1.6}
  .contact b{font-weight:700}
</style>
</head>
<body>
  <section class="card card--front" aria-label="Card front">
    <svg class="card__shape" viewBox="0 0 700 400" aria-hidden="true">
      <path d="M0 0H400C250 60 90 200 0 380Z" fill="var(--green-light)"/>
      <path d="M0 0H370C230 55 80 190 0 350Z" fill="var(--green-mid)"/>
      <path d="M0 0H340C210 55 70 180 0 320Z" fill="var(--green)"/>
    </svg>
    <div class="brand">
      <span class="brand__dot"></span>
      <span class="brand__name">MINDTRAIL</span>
    </div>
  </section>

  <section class="card card--back" aria-label="Card back">
    <svg class="card__shape" viewBox="0 0 700 400" aria-hidden="true">
      <path d="M0 150C220 150 400 250 470 400H0Z" fill="var(--green-light)"/>
      <path d="M0 170C210 172 385 265 450 400H0Z" fill="var(--green-mid)"/>
      <path d="M0 190C200 195 370 280 430 400H0Z" fill="var(--paper)"/>
    </svg>
    <div class="brand">
      <span class="brand__dot"></span>
      <span class="brand__name">MINDTRAIL</span>
    </div>
    <div class="details">
      <p class="details__name">Lee H. Corwin<small>MA</small></p>
      <p class="details__role">Licensed Professional Counselor<br>Clinical &amp; Athletic Performance Psychology</p>
      <ul class="contact">
        <li><b>Mobile:</b> 520.555.0147</li>
        <li><b>Fax:</b> 520.555.0182</li>
        <li><b>Email:</b> mindtrailleecorwin@quillpost.net</li>
        <li><b>Address:</b> 4417 East Saguaro #210 Tucson,<br>AZ 85711</li>
      </ul>
    </div>
  </section>
</body>
</html>
```